Brellwick Partners, LLC Stationary

Brellwick Partners, LLC is a new financial planning and consulting company. We are looking for designs on business cards, letterhead, envelopes, and anything else that would be useful. Our preference for business card design is two sided. We are looking for a professional and clean look with incorporating the logo and patriotic feel. Thank you to all who participate and good luck!

```html
<!DOCTYPE html>
<html lang="en">
<head>
<meta charset="utf-8">
<title>Brellwick Partners, LLC – Business Card</title>
<link href="https://fonts.googleapis.com/css2?family=Questrial&display=swap" rel="stylesheet">
<style>
  :root {
    --navy: #163b68;
    --red: #c4202b;
    --white: #ffffff;
    --ink: #3b4550;
    --page: #e9e9ec;
  }
  * { box-sizing: border-box; margin: 0; padding: 0; }
  html, body { width: 1200px; height: 950px; overflow: hidden; }
  body {
    background: var(--page);
    font-family: "Questrial", "Helvetica Neue", Arial, sans-serif;
    position: relative;
  }
  .card { position: absolute; overflow: hidden; box-shadow: 0 6px 18px rgba(0,0,0,.18); }

  /* Front */
  .card-front {
    left: 100px; top: 292px; width: 640px; height: 366px;
    background: var(--white);
  }
  .wordmark {
    position: absolute; top: 62px; left: 0; width: 100%;
    display: flex; flex-direction: column; align-items: center;
    color: var(--navy);
  }
  .wordmark-row { display: flex; align-items: center; gap: 12px; }
  .wordmark-square { width: 16px; height: 16px; background: var(--red); }
  .wordmark-name { font-size: 40px; letter-spacing: 3px; text-transform: uppercase; line-height: 1; }
  .wordmark-tagline {
    margin-top: 8px; font-size: 9px; letter-spacing: 2.4px; text-transform: uppercase;
    color: var(--navy); border-top: 1px solid var(--red); padding-top: 5px;
  }
  .divider {
    position: absolute; left: 210px; right: 40px; top: 200px;
    height: 1px; background: var(--red);
  }
  .holder { position: absolute; left: 40px; top: 188px; }
  .holder-name {
    font-size: 21px; color: var(--navy); font-variant: small-caps; letter-spacing: 1px;
  }
  .holder-title { font-size: 16px; color: var(--red); font-variant: small-caps; letter-spacing: .5px; margin-bottom: 12px; }
  .contact-list { list-style: none; font-size: 13px; color: var(--ink); }
  .contact-list li { display: flex; align-items: center; gap: 8px; height: 20px; }
  .contact-list svg { width: 11px; height: 11px; fill: var(--navy); flex: none; }
  .office {
    position: absolute; right: 40px; top: 232px; text-align: right;
    font-size: 14px; color: var(--ink); line-height: 20px;
  }
  .office-web { color: var(--navy); letter-spacing: 2px; margin-top: 6px; }
  .edge-band { position: absolute; left: 0; bottom: 0; width: 640px; height: 12px; }

  /* Back */
  .card-back {
    left: 800px; top: 212px; width: 300px; height: 525px;
    background: var(--navy); color: var(--white);
  }
  .back-field {
    position: absolute; left: 0; top: 0; width: 300px; height: 300px;
  }
  .back-wordmark {
    position: absolute; left: 0; right: 0; top: 360px;
    display: flex; flex-direction: column; align-items: center; text-align: center;
  }
  .back-name { font-size: 32px; letter-spacing: 2px; text-transform: uppercase; line-height: 1.05; }
  .back-tagline {
    margin-top: 10px; font-size: 8px; letter-spacing: 2px; text-transform: uppercase;
    border-top: 1px solid var(--white); padding-top: 5px;
  }
  .back-web { margin-top: 14px; font-size: 13px; letter-spacing: 3px; }
</style>
</head>
<body>

<section class="card card-front" aria-label="Business card front">
  <div class="wordmark">
    <div class="wordmark-row">
      <span class="wordmark-square"></span>
      <span class="wordmark-name">Brellwick</span>
    </div>
    <div class="wordmark-name" style="font-size:20px;letter-spacing:4px;margin-top:6px;">Partners, LLC</div>
    <div class="wordmark-tagline">Financial Planning and Consulting</div>
  </div>

  <div class="divider"></div>

  <div class="holder">
    <p class="holder-name">Dana Marlow</p>
    <p class="holder-title">CEO/Founder</p>
    <ul class="contact-list">
      <li><svg viewBox="0 0 24 24"><path d="M6.6 10.8a15 15 0 0 0 6.6 6.6l2.2-2.2a1 1 0 0 1 1-.25 11.4 11.4 0 0 0 3.6.57 1 1 0 0 1 1 1V20a1 1 0 0 1-1 1A17 17 0 0 1 3 4a1 1 0 0 1 1-1h3.5a1 1 0 0 1 1 1c0 1.25.2 2.45.57 3.57a1 1 0 0 1-.25 1z"/></svg>555 214 7781</li>
      <li><svg viewBox="0 0 24 24"><path d="M6 2h12v6H6zM3 9h18v10h-3v3H6v-3H3zm5 6v5h8v-5z"/></svg>555 390 6625</li>
      <li><svg viewBox="0 0 24 24"><path d="M2 5h20v14H2zm2 2v.5l8 5 8-5V7z"/></svg>dana@brellwick.com</li>
    </ul>
  </div>

  <div class="office">
    <p>412 Harbor Ridge Road</p>
    <p>Juneau, Alaska 99801</p>
    <p class="office-web">www.brellwick.com</p>
  </div>

  <svg class="edge-band" viewBox="0 0 640 12" preserveAspectRatio="none" aria-hidden="true">
    <polygon points="0,0 360,0 372,12 0,12" fill="var(--navy)"/>
    <polygon points="360,0 640,0 640,12 372,12" fill="var(--red)"/>
  </svg>
</section>

<section class="card card-back" aria-label="Business card back">
  <svg class="back-field" viewBox="0 0 300 300" role="img" aria-label="Large brand symbol area in red, white and navy">
    <defs>
      <linearGradient id="symbolTone" x1="0" y1="0" x2="0" y2="1">
        <stop offset="0" stop-color="#c4202b"/>
        <stop offset="1" stop-color="#163b68"/>
      </linearGradient>
    </defs>
    <rect width="300" height="300" fill="url(#symbolTone)"/>
  </svg>
  <div class="back-wordmark">
    <p class="back-name">Brellwick</p>
    <p class="back-name" style="font-size:17px;letter-spacing:4px;margin-top:6px;">Partners, LLC</p>
    <p class="back-tagline">Financial Planning and Consulting</p>
    <p class="back-web">www.brellwick.com</p>
  </div>
</section>

</body>
</html>
```